Modern Business Card for Larkwell 2018

Our company assumes the best about people. We are creating an online community of entrepreneurs and business leaders who struggle with marketing their business online.

This business card should POP! We recently got a new logo and are launching a new website next month, so our business cards should make a statement that feels:
-Fresh
-Smart
-Trustworthy
-Fun

Target Market(s)

small business owners, entrepreneurs

Industry/Entity Type

Digital Marketing

Contact Information for Business Card

Dimensions: 3.5" x 2"

Font styles to use
Sans Serif

Colors
f37122
ffffff

Requirements
Must have
• We need a business card with a modern, bold design. We will use one side of the card as a lead-generation offer, so text on one side will need to fit up to 140 characters. The business card should stick to our core colors (orange, black, and white).
Nice to have
• We think a vertical "portrait" design could be interesting.
Should not have
• Should not look like a traditional business card. The round icon should stand out from a distance.

```html
<!DOCTYPE html>
<html lang="en">
<head>
<meta charset="utf-8">
<title>Larkwell Business Card</title>
<link rel="stylesheet" href="https://fonts.googleapis.com/css2?family=Roboto:wght@400;500;700;900&family=Kaushan+Script&display=swap">
<style>
  :root {
    --orange: #f26a26;
    --white: #ffffff;
    --paper: #f3f3f3;
    --ink: #151515;
    --backdrop: #e9e4de;
  }
  * { margin: 0; padding: 0; box-sizing: border-box; }
  html, body { width: 1200px; height: 960px; overflow: hidden; }
  body {
    position: relative;
    background: var(--backdrop);
    font-family: "Roboto", Arial, sans-serif;
  }
  .card {
    position: absolute;
    width: 600px;
    height: 342px;
    border-radius: 20px;
    overflow: hidden;
  }
  /* Front */
  .card-front { left: 314px; top: 113px; background: var(--paper); }
  .card-front .wave { position: absolute; inset: 0; }
  .brand-mark {
    position: absolute; left: 64px; top: 67px;
    display: flex; align-items: center; gap: 16px;
  }
  .brand-dot {
    width: 110px; height: 110px; border-radius: 50%;
    background: var(--orange);
  }
  .brand-name-front {
    font-weight: 900; font-size: 30px; color: var(--orange);
    letter-spacing: 1px;
  }
  .person {
    position: absolute; right: 21px; top: 218px; text-align: right;
  }
  .person-name {
    font-family: "Kaushan Script", cursive;
    font-size: 33px; line-height: 44px; color: var(--ink);
    white-space: nowrap;
  }
  .person-role {
    font-size: 19px; font-weight: 500; color: var(--ink);
    letter-spacing: 0.3px; line-height: 24px;
  }
  .person-email {
    font-size: 14px; font-weight: 700; color: var(--ink);
    margin-top: 6px;
  }
  /* Back */
  .card-back { left: 311px; top: 472px; background: var(--orange); color: var(--white); }
  .back-brand {
    position: absolute; left: 30px; top: 58px; width: 258px;
    text-align: center;
  }
  .back-dot {
    width: 36px; height: 36px; border-radius: 50%;
    background: var(--white); margin: 0 auto 6px;
  }
  .brand-name-back {
    font-weight: 900; font-size: 38px; line-height: 40px; letter-spacing: 1.5px;
  }
  .brand-tagline {
    font-size: 11.5px; font-weight: 700; letter-spacing: 1.2px; margin-top: 4px;
  }
  .divider {
    position: absolute; left: 297px; top: 28px; width: 1px; height: 162px;
    background: rgba(255,255,255,0.55);
  }
  .offer { position: absolute; left: 323px; top: 28px; width: 260px; }
  .offer-headline {
    font-size: 18px; font-weight: 700; line-height: 21px; letter-spacing: 0.3px;
  }
  .offer-body { font-size: 15px; line-height: 19px; margin-top: 6px; }
  .offer-url { font-size: 19px; font-weight: 700; margin-top: 11px; }
  .notes {
    position: absolute; left: 20px; top: 217px; width: 557px; height: 101px;
    background: var(--white); border-radius: 18px;
  }
  .notes-line {
    position: absolute; left: 24px; right: 28px; height: 1px; background: var(--ink);
  }
  .notes-line.first { top: 31px; }
  .notes-line.second { top: 71px; }
</style>
</head>
<body>
  <section class="card card-front" aria-label="Business card front">
    <svg class="wave" viewBox="0 0 600 342" width="600" height="342" aria-hidden="true">
      <path d="M0,212 C100,290 190,285 295,200 S495,45 600,42 L600,342 L0,342 Z" fill="var(--ink)"/>
      <path d="M0,250 C90,296 190,296 300,211 S500,56 600,56 L600,342 L0,342 Z" fill="var(--white)"/>
      <path d="M0,254 C90,300 190,300 300,215 S500,60 600,60 L600,342 L0,342 Z" fill="var(--orange)"/>
    </svg>
    <div class="brand-mark">
      <div class="brand-dot"></div>
      <div class="brand-name-front">LARKWELL</div>
    </div>
    <div class="person">
      <div class="person-name">DANA WHITFIELD</div>
      <div class="person-role">STORY MARKETING COACH</div>
      <div class="person-email">dana@larkwellnow.com</div>
    </div>
  </section>

  <section class="card card-back" aria-label="Business card back">
    <div class="back-brand">
      <div class="back-dot"></div>
      <div class="brand-name-back">LARKWELL</div>
      <div class="brand-tagline">TELL STORIES THAT INSPIRE ACTION</div>
    </div>
    <div class="divider"></div>
    <div class="offer">
      <div class="offer-headline">REACH MORE PEOPLE.<br>MAKE MORE MONEY.<br>CREATE MORE IMPACT.</div>
      <div class="offer-body">Get your free Larkwell<br>Starter Package and our<br>marketing guide today at</div>
      <div class="offer-url">Larkwellnow.com/start</div>
    </div>
    <div class="notes">
      <div class="notes-line first"></div>
      <div class="notes-line second"></div>
    </div>
  </section>
</body>
</html>
```